Healthcare technology firm needs business card layout. Logo provided.

We need a business card design for a new healthcare technology company called BelnaVix.net. The logo is already done so that will be used in the design. We assist patients and their families manage their personal health finances. Our initial product is our web site membership that includes educational content on your health benefits, tools, and downloadable forms.

We would like to see designs that use our existing logo or extend the logo in a creative way. Should be very consumer friendly.

Industry/Entity Type

Healthcare

```html
<!DOCTYPE html>
<html lang="en">
<head>
<meta charset="utf-8">
<title>BelnaVix Business Card</title>
<link rel="stylesheet" href="https://fonts.googleapis.com/css2?family=Questrial&family=Arimo:wght@400&display=swap">
<style>
  :root {
    --page-bg: #ffffff;
    --card-white: #ffffff;
    --brand-blue: #0d35f5;
    --logo-blue: #1a55e8;
    --tagline-blue: #1238e0;
    --brand-green: #35ff35;
    --text-white: #ffffff;
    --site-green: #b4f7ac;
  }
  * { margin: 0; padding: 0; box-sizing: border-box; }
  html, body {
    width: 1200px;
    height: 900px;
    overflow: hidden;
    background: var(--page-bg);
  }
  .canvas {
    position: relative;
    width: 1200px;
    height: 900px;
  }
  .business-card {
    position: absolute;
    left: 66px;
    top: 127px;
    width: 1062px;
    height: 649px;
    background: var(--card-white);
    box-shadow: 2px 3px 6px rgba(0, 0, 0, 0.18);
  }
  .brand-panel {
    position: absolute;
    left: 0;
    top: 0;
    width: 492px;
    height: 649px;
    background: var(--card-white);
  }
  .wordmark {
    position: absolute;
    left: 0;
    top: 222px;
    width: 492px;
    text-align: center;
    font-family: "Questrial", sans-serif;
    font-size: 92px;
    line-height: 1;
    letter-spacing: 1px;
    color: var(--logo-blue);
  }
  .tagline {
    position: absolute;
    left: 0;
    top: 366px;
    width: 494px;
    text-align: center;
    font-family: "Questrial", sans-serif;
    font-size: 25px;
    color: var(--tagline-blue);
  }
  .accent-bar {
    position: absolute;
    left: 492px;
    top: 0;
    width: 30px;
    height: 649px;
    background: var(--brand-blue);
  }
  .identity-panel,
  .contact-panel {
    position: absolute;
    left: 530px;
    width: 532px;
    background: var(--brand-green);
    color: var(--text-white);
  }
  .identity-panel { top: 0; height: 320px; }
  .contact-panel { top: 328px; height: 321px; }
  .person-name {
    position: absolute;
    left: 24px;
    top: 224px;
    font-family: "Arimo", sans-serif;
    font-size: 33px;
    line-height: 1;
  }
  .person-title {
    position: absolute;
    left: 24px;
    top: 267px;
    font-family: "Arimo", sans-serif;
    font-size: 22px;
    line-height: 1;
  }
  .office-list {
    position: absolute;
    left: 24px;
    top: 40px;
    width: 400px;
    font-family: "Questrial", sans-serif;
    font-size: 22px;
    line-height: 30px;
    letter-spacing: 1.2px;
  }
  .phone {
    position: absolute;
    left: 24px;
    top: 113px;
    font-family: "Questrial", sans-serif;
    font-size: 22px;
    letter-spacing: 1.2px;
  }
  .website {
    position: absolute;
    left: 24px;
    top: 236px;
    font-family: "Questrial", sans-serif;
    font-size: 62px;
    line-height: 1;
    letter-spacing: 1.5px;
    color: var(--site-green);
  }
</style>
</head>
<body>
<main class="canvas">
  <section class="business-card">
    <div class="brand-panel">
      <div class="wordmark">BelnaVix</div>
      <p class="tagline">Helping your family plan for care.</p>
    </div>
    <div class="accent-bar"></div>
    <div class="identity-panel">
      <p class="person-name">Maren T. Holt</p>
      <p class="person-title">CEO</p>
    </div>
    <div class="contact-panel">
      <p class="office-list">Fairhaven Cedar Bluff Marlow Port Elston</p>
      <p class="phone">M: 555-310-4827</p>
      <p class="website">belnavix.net</p>
    </div>
  </section>
</main>
</body>
</html>
```